Bref créative
Letterhead and Business Cards
Bookkeeping Business
Professional
Marcus J Whitfield
Business Advisor
527 Linden Avenue - Suite 200
Bakersfield, CA 93412
Marcus@KRLedgerworks.com
www.KRLedgerworks.com
I will upload the logo that I would like to use on my business card in AI format
Would like to include the FTB e-submit logo and the Certified LedgerPilot TrustPartner logo on the back of my card.
Also - reference to the following:
Monthly bookkeeping with financial statement preparation
Individual, corporate & partnership taxes
Payroll services
Business consulting

```html
<!DOCTYPE html>
<html lang="en">
<head>
<meta charset="utf-8">
<title>KRLedger Stationery</title>
<link rel="stylesheet" href="https://fonts.googleapis.com/css2?family=Open+Sans:wght@400;600;700&display=swap">
<style>
  :root {
    --backdrop: #dcc7a4;
    --paper: #ffffff;
    --navy: #1f3d73;
    --blue: #2b67b2;
    --green: #5ea83c;
    --ink: #4a5563;
    --faint: #e6ecf4;
    --edge: rgba(0,0,0,0.12);
  }
  * { box-sizing: border-box; margin: 0; padding: 0; }
  html, body { width: 1200px; height: 446px; overflow: hidden; }
  body {
    background: var(--backdrop);
    font-family: "Open Sans", Arial, sans-serif;
    color: var(--ink);
    position: relative;
  }
  .sheet {
    position: absolute;
    background: var(--paper);
    box-shadow: 0 1px 3px var(--edge);
    overflow: hidden;
  }
  .brand {
    display: flex; align-items: center; gap: 5px;
    font-weight: 700; color: var(--navy); white-space: nowrap;
  }
  .brand-square { background: var(--blue); flex: none; }
  .wave { position: absolute; left: 0; bottom: 0; width: 100%; display: block; }
  .contact { font-size: 4.5px; line-height: 1.5; color: var(--ink); }
  .watermark {
    position: absolute; left: 0; right: 0; text-align: center;
    font-weight: 700; color: var(--faint); font-size: 44px;
  }

  /* business cards */
  .card { left: 19px; width: 101px; height: 62px; }
  .card-front { top: 216px; }
  .card-back { top: 300px; }
  .card .brand { position: absolute; left: 7px; top: 8px; font-size: 10px; }
  .card .brand-square { width: 9px; height: 9px; }
  .card-back .brand { left: 50%; transform: translateX(-50%); top: 10px; font-size: 9px; }
  .card-back .services { position: absolute; top: 26px; left: 0; right: 0; text-align: center; font-size: 3.6px; line-height: 1.45; }

  /* letterheads */
  .letterhead { top: 19px; width: 300px; height: 420px; }
  .letterhead-one { left: 163px; }
  .letterhead-two { left: 475px; }
  .letterhead-one .brand { position: absolute; left: 18px; top: 16px; font-size: 13px; }
  .letterhead .brand-square { width: 12px; height: 12px; }
  .letterhead-one .contact { position: absolute; right: 18px; top: 18px; text-align: left; }
  .letterhead-two .brand { position: absolute; left: 50%; transform: translateX(-50%); top: 18px; font-size: 13px; }
  .letterhead-two .contact { position: absolute; left: 0; right: 0; bottom: 56px; text-align: center; }
  .letterhead .watermark { top: 185px; }

  /* envelopes */
  .envelope-backs { position: absolute; left: 792px; top: 12px; width: 392px; height: 192px; }
  .envelope-front { left: 792px; top: 264px; width: 392px; height: 137px; }
  .envelope-front .brand { position: absolute; left: 14px; top: 14px; font-size: 12px; }
  .envelope-front .brand-square { width: 11px; height: 11px; }
  .envelope-front .contact { position: absolute; left: 14px; top: 32px; }
</style>
</head>
<body>

<svg width="0" height="0" style="position:absolute">
  <defs>
    <symbol id="footer-wave" viewBox="0 0 300 60" preserveAspectRatio="none">
      <path d="M0 22 C90 52 200 8 300 30 L300 60 L0 60 Z" fill="var(--green)"/>
      <path d="M0 34 C100 60 210 20 300 40 L300 60 L0 60 Z" fill="var(--blue)"/>
      <path d="M0 30 C95 56 205 14 300 35" fill="none" stroke="#fff" stroke-width="1.2"/>
    </symbol>
  </defs>
</svg>

<!-- Business card front -->
<div class="sheet card card-front">
  <div class="brand"><span class="brand-square"></span>KRLedger</div>
  <svg class="wave" height="16"><use href="#footer-wave"/></svg>
</div>

<!-- Business card back -->
<div class="sheet card card-back">
  <div class="brand"><span class="brand-square"></span>KRLedger</div>
  <div class="services">Monthly bookkeeping &amp; financial statements<br>Individual, corporate &amp; partnership taxes<br>Payroll services · Business consulting</div>
  <svg class="wave" height="12"><use href="#footer-wave"/></svg>
</div>

<!-- Letterhead option 1 -->
<div class="sheet letterhead letterhead-one">
  <div class="brand"><span class="brand-square"></span>KRLedger</div>
  <div class="contact">527 Linden Avenue - Suite 200<br>Bakersfield, CA 93412<br>Marcus@KRLedgerworks.com<br>www.KRLedgerworks.com</div>
  <div class="watermark">KRLedger</div>
  <svg class="wave" height="46"><use href="#footer-wave"/></svg>
</div>

<!-- Letterhead option 2 -->
<div class="sheet letterhead letterhead-two">
  <div class="brand"><span class="brand-square"></span>KRLedger</div>
  <div class="watermark">KRLedger</div>
  <div class="contact">527 Linden Avenue - Suite 200, Bakersfield, CA 93412 · Marcus@KRLedgerworks.com · www.KRLedgerworks.com</div>
  <svg class="wave" height="46"><use href="#footer-wave"/></svg>
</div>

<!-- Envelope backs -->
<svg class="envelope-backs" viewBox="0 0 392 192">
  <rect x="0" y="0" width="392" height="70" fill="#fff"/>
  <path d="M0 0 H392 V22 C270 44 120 44 0 22 Z" fill="var(--blue)"/>
  <rect x="0" y="58" width="392" height="70" fill="#fff"/>
  <path d="M0 58 H392 V82 C270 104 120 104 0 82 Z" fill="var(--green)"/>
  <rect x="0" y="118" width="392" height="74" fill="#fff"/>
  <path d="M0 118 L196 158 L392 118" fill="none" stroke="#dde3ea" stroke-width="1"/>
  <rect x="164" y="143" width="9" height="9" fill="var(--blue)"/>
  <text x="177" y="151" font-family="Open Sans, Arial, sans-serif" font-weight="700" font-size="10" fill="var(--navy)">KRLedger</text>
</svg>

<!-- Envelope front -->
<div class="sheet envelope-front">
  <div class="brand"><span class="brand-square"></span>KRLedger</div>
  <div class="contact">527 Linden Avenue - Suite 200<br>Bakersfield, CA 93412</div>
  <svg class="wave" height="30"><use href="#footer-wave"/></svg>
</div>

</body>
</html>
```